Verlindo Magician

I want the business card for my business to give to people who watch that later I will be employed to show magic here is my website http://www.balsamomagicien.com/I want the interesting design , i am very opened for formal and informal, I watch a lot of design so don't stick to the common shape and form but i hope it can also be produced the thing to write on will be the same as in picture that i will upload , i also will upload the logo for you that so can be easy to useDenis CostilleMagicianMAGICIAN BALSAMO 17 rue des Tilleuls - 25000 BESANÇON contact@verlindoillusions.example tel. 0381 946 157 tel. 0674 219 503

```html
<!DOCTYPE html>
<html lang="fr">
<head>
<meta charset="utf-8">
<title>Verlindo Magician – Business Card</title>
<link href="https://fonts.googleapis.com/css2?family=Open+Sans:wght@300;400;700&display=swap" rel="stylesheet">
<style>
  :root {
    --ink: #0b0b0b;
    --paper: #ffffff;
    --red: #d0312d;
    --grey: #3a3a3a;
    --stage: #ece9e4;
  }
  * { margin: 0; padding: 0; box-sizing: border-box; }
  html, body { width: 1200px; height: 900px; overflow: hidden; }
  body {
    background: var(--stage);
    font-family: "Open Sans", Arial, sans-serif;
    position: relative;
  }
  .card {
    position: absolute;
    width: 600px;
    height: 360px;
    border-radius: 4px;
    overflow: hidden;
    box-shadow: 0 6px 18px rgba(0,0,0,0.18);
  }
  .brand {
    color: var(--paper);
    text-align: center;
    line-height: 1;
  }
  .brand-name {
    display: block;
    font-weight: 300;
    letter-spacing: 2px;
  }
  .brand-tag {
    display: block;
    font-weight: 400;
    letter-spacing: 1.5px;
    margin-top: 3px;
  }

  /* Front side */
  .card-front {
    left: 110px;
    top: 80px;
    background: var(--ink);
  }
  .card-front .portrait {
    position: absolute;
    left: 225px;
    top: 55px;
    width: 150px;
    height: 165px;
    border-radius: 60px 60px 14px 14px;
    background: linear-gradient(180deg, #f4f4f4, #d9d9d9);
  }
  .card-front .brand {
    position: absolute;
    left: 0;
    right: 0;
    top: 232px;
  }
  .card-front .brand-name { font-size: 30px; }
  .card-front .brand-tag { font-size: 10px; }

  /* Back side */
  .card-back {
    left: 500px;
    top: 440px;
    background: var(--paper);
  }
  .card-back .swoosh {
    position: absolute;
    inset: 0;
    width: 100%;
    height: 100%;
  }
  .card-back .portrait {
    position: absolute;
    left: 405px;
    top: 40px;
    width: 150px;
    height: 165px;
    border-radius: 60px 60px 14px 14px;
    background: linear-gradient(180deg, #2a2a2a, #0b0b0b);
  }
  .card-back .brand {
    position: absolute;
    right: 28px;
    top: 284px;
    width: 150px;
  }
  .card-back .brand-name { font-size: 26px; }
  .card-back .brand-tag { font-size: 9px; }

  .details {
    position: absolute;
    left: 52px;
    top: 56px;
    color: var(--grey);
  }
  .details .name {
    color: var(--red);
    font-weight: 700;
    font-size: 22px;
    line-height: 30px;
    letter-spacing: 0.5px;
  }
  .details .role {
    font-size: 14px;
    line-height: 18px;
    margin-left: 12px;
    margin-bottom: 10px;
  }
  .contact-list {
    list-style: none;
    margin-left: 16px;
    font-size: 15px;
    line-height: 22px;
  }
  .contact-list li { display: flex; align-items: center; gap: 7px; }
  .contact-list svg { width: 14px; height: 14px; flex: none; }
  .company {
    margin-left: 40px;
    margin-top: 6px;
    color: var(--red);
    font-weight: 700;
    font-size: 15px;
    line-height: 20px;
  }
  .address {
    margin-left: 40px;
    font-size: 15px;
    line-height: 20px;
  }
</style>
</head>
<body>

  <section class="card card-front">
    <div class="portrait" role="img" aria-label="Illustration of the magician holding a playing card"></div>
    <div class="brand">
      <span class="brand-name">VERLINDO</span>
      <span class="brand-tag">MAGICIAN</span>
    </div>
  </section>

  <section class="card card-back">
    <svg class="swoosh" viewBox="0 0 600 360" preserveAspectRatio="none" aria-hidden="true">
      <path d="M0,316 C250,330 450,268 600,168 L600,182 C450,284 250,344 0,334 Z" fill="var(--red)"/>
      <path d="M0,344 C250,352 460,290 600,196 L600,360 L0,360 Z" fill="var(--ink)"/>
    </svg>

    <div class="portrait" role="img" aria-label="Illustration of the magician holding a playing card"></div>

    <div class="details">
      <div class="name">MARC RAVOULET</div>
      <div class="role">Magician</div>
      <ul class="contact-list">
        <li>
          <svg viewBox="0 0 16 16"><path fill="var(--red)" d="M2 5c0-2 2-3 6-3s6 1 6 3l-2 1-1-2H5L4 6 2 5Zm2 2h8l1 6H3l1-6Zm4 1.5a2 2 0 1 0 0 4 2 2 0 0 0 0-4Z"/></svg>
          0381 946 157
        </li>
        <li>
          <svg viewBox="0 0 16 16"><path fill="var(--red)" d="M2 5c0-2 2-3 6-3s6 1 6 3l-2 1-1-2H5L4 6 2 5Zm2 2h8l1 6H3l1-6Zm4 1.5a2 2 0 1 0 0 4 2 2 0 0 0 0-4Z"/></svg>
          0674 219 503
        </li>
        <li>
          <svg viewBox="0 0 16 16"><rect x="1" y="3" width="14" height="10" fill="var(--red)"/><path d="M1.5 3.5 8 9l6.5-5.5" stroke="#fff" stroke-width="1.3" fill="none"/></svg>
          contact@verlindoillusions.example
        </li>
        <li>
          <svg viewBox="0 0 16 16"><circle cx="8" cy="8" r="7" fill="var(--red)"/><path d="M4 6h4l1 3-2 3M9 3l2 2h2" stroke="#fff" stroke-width="1.2" fill="none"/></svg>
          www.verlindoillusions.example
        </li>
      </ul>
      <div class="company">MAGICIAN VERLINDO</div>
      <div class="address">17 rue des Tilleuls - 25000<br>BESANÇON</div>
    </div>

    <div class="brand">
      <span class="brand-name">VERLINDO</span>
      <span class="brand-tag">MAGICIAN</span>
    </div>
  </section>

</body>
</html>
```